Refresh Application User Interface

Brightmoor wishes to update the look of its business applications. Two representative forms are shown below. Please note, we are not considering changes in functionality or usability. Our goal is a cleaner, more contemporary design.

Industry/Entity Type

Business

```html
<!DOCTYPE html>
<html lang="en">
<head>
<meta charset="utf-8">
<title>Brightmoor – Purchase Order</title>
<link href="https://fonts.googleapis.com/css2?family=Lato:wght@400;700&display=swap" rel="stylesheet">
<style>
:root{
  --black:#000;
  --page:#f2f2f2;
  --white:#fff;
  --green:#7ccc3a;
  --blue:#1256c4;
  --navy:#0b4aa8;
  --link:#1257c6;
  --text:#222;
  --border:#cfcfcf;
}
*{box-sizing:border-box;margin:0;padding:0}
html,body{width:1200px;height:1151px;overflow:hidden;background:var(--page);font-family:'Lato',sans-serif;color:var(--text)}
.stage{position:absolute;left:0;top:0;width:1300px;height:1247px;transform:scale(.923077);transform-origin:0 0;background:var(--page)}
.abs{position:absolute}
.topbar{left:0;top:0;width:1300px;height:50px;background:var(--black);color:#ddd;font-size:14px}
.topbar .who{left:81px;top:17px}
.topbar b{color:#fff}
.topbar .role{left:272px;top:17px}
.topbar .links{right:76px;top:17px}
.apptabs .tab{top:79px;height:41px;background:#f7f7f7;border:1px solid var(--border);border-bottom:none;font-weight:700;font-size:15px;display:flex;align-items:center;justify-content:center;color:var(--text)}
.apptabs .tab.active{background:var(--green);color:#fff;border-color:var(--green)}
.brand{left:1064px;top:70px;font-size:27px;font-weight:700;color:var(--navy);letter-spacing:1px}
.subnav{left:0;top:119px;width:1300px;height:48px;background:var(--green);color:#fff;font-weight:700;font-size:15px}
.subnav span{position:absolute;top:16px}
.pagehead{left:81px;top:180px;font-size:25px;color:#333}
.viewtab{top:181px;height:41px;border:1px solid var(--border);border-bottom:none;background:#f7f7f7;font-weight:700;font-size:15px;display:flex;align-items:center;justify-content:center}
.viewtab.active{background:var(--blue);color:#fff;border-color:var(--blue)}
.dot{display:inline-block;width:11px;height:11px;border-radius:50%;background:var(--green);margin-left:2px;margin-top:-10px}
.toolbar{left:0;top:221px;width:1300px;height:48px;background:var(--blue);color:#fff;font-weight:700;font-size:15px}
.toolbar .btn{position:absolute;top:0;height:48px;display:flex;align-items:center;gap:8px;padding:0 14px;border-right:1px solid rgba(255,255,255,.25)}
.toolbar svg{width:15px;height:15px;fill:none;stroke:#fff;stroke-width:2.2}
.card{left:81px;top:292px;width:1139px;height:918px;background:var(--white);border:1px solid var(--border)}
.lbl{font-weight:700;font-size:15px;color:var(--text)}
.field{height:37px;border:1px solid var(--border);background:#fff;font-size:15px;padding:0 12px;display:flex;align-items:center;color:var(--text)}
.select{justify-content:space-between;padding-right:14px}
.link{color:var(--link);font-size:15px}
.formtab{top:742px;height:37px;background:var(--navy);color:#fff;font-weight:700;font-size:15px;display:flex;align-items:center;justify-content:center}
.formtab.active{background:#f7f7f7;color:var(--text);border:1px solid var(--border);border-bottom:none;height:38px}
.panel{left:126px;top:779px;width:1027px;height:360px;border:1px solid var(--border);background:#fff}
.req{font-size:13px}
.arrows{width:8px;height:14px}
</style>
</head>
<body>
<div class="stage">
  <div class="abs topbar">
    <div class="abs who">Logged in as <b>Dana Reyes</b> &#9881;</div>
    <div class="abs role">Current Role <b>Administrator</b> &#8964;</div>
    <div class="abs links">Touch &nbsp;/&nbsp; New Tab &nbsp;/&nbsp; Help &nbsp;/&nbsp; Support &nbsp;/&nbsp; Log Out</div>
  </div>

  <div class="apptabs">
    <div class="abs tab" style="left:80px;width:83px">Home</div>
    <div class="abs tab" style="left:170px;width:83px">eSource</div>
    <div class="abs tab active" style="left:261px;width:81px">eBuy</div>
    <div class="abs tab" style="left:350px;width:93px">eRequest</div>
    <div class="abs tab" style="left:450px;width:83px">eStock</div>
    <div class="abs tab" style="left:540px;width:83px">ePlan</div>
    <div class="abs tab" style="left:631px;width:113px">Preference</div>
  </div>
  <div class="abs brand">BRIGHTMOOR</div>

  <div class="abs subnav">
    <span style="left:81px">Order</span><span style="left:153px">Receipt</span><span style="left:236px">Shipments</span>
    <span style="left:340px">Invoices &nbsp;|</span><span style="left:432px">Pricing</span><span style="left:511px">Tables</span>
    <span style="left:585px">Reports</span><span style="left:671px">Injuiries</span><span style="left:758px">Periodic Task</span><span style="left:881px">Workflows</span>
  </div>

  <div class="abs pagehead">Purchase Order</div>
  <div class="abs viewtab active" style="left:871px;width:81px">Header</div>
  <div class="abs viewtab" style="left:959px;width:83px">Lines<span class="dot"></span></div>
  <div class="abs viewtab" style="left:1049px;width:83px">Charges</div>
  <div class="abs viewtab" style="left:1139px;width:82px">Notes<span class="dot"></span></div>

  <div class="abs toolbar">
    <div class="btn" style="left:66px;width:52px"><svg viewBox="0 0 16 16"><path d="M10 4 5 9a2 2 0 0 0 3 3l5-6a3 3 0 0 0-5-4L3 8"/></svg></div>
    <div class="btn" style="left:118px;width:55px"><svg viewBox="0 0 16 16"><path d="M2 2h7M2 6h5M2 10h4"/><circle cx="11" cy="10" r="3"/><path d="m13 12 2 2"/></svg></div>
    <div class="btn" style="left:173px;width:50px"><svg viewBox="0 0 16 16"><circle cx="4" cy="8" r="2"/><circle cx="12" cy="3" r="2"/><circle cx="12" cy="13" r="2"/><path d="m6 7 4-3M6 9l4 3"/></svg></div>
    <div class="btn" style="left:223px;width:55px"><svg viewBox="0 0 16 16"><path d="M8 1 14 4v8L8 15 2 12V4z"/><path d="M2 4l6 3 6-3M8 7v8"/></svg></div>
    <div class="btn" style="left:278px;width:55px"><svg viewBox="0 0 16 16"><circle cx="8" cy="8" r="6.5"/><path d="M6 6a2 2 0 1 1 2 2v1.5M8 11.5v1"/></svg></div>
    <div class="btn" style="left:333px;width:159px"><svg viewBox="0 0 16 16"><circle cx="7" cy="7" r="5"/><path d="m11 11 4 4"/></svg>View GL Order</div>
    <div class="btn" style="left:492px;width:140px;border-right:none"><svg viewBox="0 0 16 16"><rect x="2" y="2" width="12" height="12" rx="2"/><path d="m6 10 4-4"/></svg>Post Order</div>
    <div class="btn" style="left:753px;width:108px;border-left:1px solid rgba(255,255,255,.25)"><svg viewBox="0 0 16 16"><circle cx="7" cy="7" r="5"/><path d="m11 11 4 4"/></svg>Search</div>
    <div class="btn" style="left:861px;width:93px"><svg viewBox="0 0 16 16"><circle cx="8" cy="8" r="6.5"/><path d="M8 5v6M5 8h6"/></svg>New</div>
    <div class="btn" style="left:954px;width:103px"><svg viewBox="0 0 16 16"><circle cx="7" cy="7" r="5"/><path d="m11 11 4 4"/></svg>Apply</div>
    <div class="btn" style="left:1057px;width:95px">X&nbsp; Delete</div>
    <div class="btn" style="left:1152px;width:90px;border-right:none"><svg viewBox="0 0 16 16"><path d="M6 3 2 7l4 4M2 7h8a4 4 0 0 1 4 4v2"/></svg>Back</div>
  </div>

  <div class="abs card"></div>

  <div class="abs lbl" style="left:114px;top:336px">Order #</div>
  <div class="abs link" style="left:222px;top:336px">100159</div>
  <div class="abs lbl" style="left:114px;top:377px">Ship From</div>
  <div class="abs field" style="left:222px;top:368px;width:151px;height:36px">1001</div>
  <div class="abs" style="left:385px;top:377px;font-size:15px">/</div>
  <div class="abs field" style="left:397px;top:368px;width:42px;height:36px;justify-content:center">1</div>
  <div class="abs field" style="left:222px;top:423px;width:533px">Harbor Care Supply Inc.</div>
  <div class="abs lbl" style="left:126px;top:485px">Address</div>
  <div class="abs field" style="left:222px;top:476px;width:533px">14 Linden Way</div>
  <div class="abs field" style="left:222px;top:529px;width:533px"></div>
  <div class="abs link" style="left:776px;top:539px">DVP Unconfirmed</div>
  <div class="abs lbl" style="left:154px;top:592px">City</div>
  <div class="abs field" style="left:222px;top:583px;width:340px">Westbrook</div>
  <div class="abs lbl" style="left:581px;top:591px">State</div>
  <div class="abs field" style="left:632px;top:583px;width:52px">MA</div>
  <div class="abs" style="left:777px;top:593px;font-size:15px;display:flex;align-items:center;gap:8px">
    <svg width="13" height="13" viewBox="0 0 13 13"><rect width="13" height="13" rx="2" fill="#222"/><path d="m3 6.5 2.5 2.5L10 4" stroke="#fff" stroke-width="2" fill="none"/></svg>Accept</div>
  <div class="abs lbl" style="left:161px;top:644px">Zip</div>
  <div class="abs field" style="left:222px;top:636px;width:151px;height:36px">01882-4410</div>
  <div class="abs lbl" style="left:392px;top:644px">Country</div>
  <div class="abs field" style="left:463px;top:636px;width:52px;height:36px;justify-content:center">US</div>
  <div class="abs link" style="left:531px;top:646px">Add Contact</div>

  <div class="abs formtab" style="left:127px;width:108px">Order Info</div>
  <div class="abs formtab active" style="left:246px;width:110px">Shipping</div>
  <div class="abs formtab" style="left:365px;width:108px">Payments</div>
  <div class="abs formtab" style="left:483px;width:109px">Accounts</div>
  <div class="abs formtab" style="left:601px;width:156px">Totals/ Approval</div>
  <div class="abs panel"></div>

  <div class="abs lbl" style="left:194px;top:823px">Receive at</div>
  <div class="abs field select" style="left:283px;top:815px;width:151px">ALCH<svg class="arrows" viewBox="0 0 8 14"><path d="M0 6 4 1l4 5zM0 8l4 5 4-5z" fill="#222"/></svg></div>
  <div class="abs req" style="left:443px;top:826px">*</div>
  <div class="abs lbl" style="left:216px;top:870px">Carrier</div>
  <div class="abs field select" style="left:283px;top:862px;width:151px">Swiftline<svg class="arrows" viewBox="0 0 8 14"><path d="M0 6 4 1l4 5zM0 8l4 5 4-5z" fill="#222"/></svg></div>
  <div class="abs req" style="left:443px;top:876px">*</div>
  <div class="abs lbl" style="left:157px;top:917px">Express Service</div>
  <div class="abs field select" style="left:283px;top:909px;width:151px"><span></span><svg class="arrows" viewBox="0 0 8 14"><path d="M0 6 4 1l4 5zM0 8l4 5 4-5z" fill="#222"/></svg></div>
  <div class="abs lbl" style="left:236px;top:964px">FOB</div>
  <div class="abs field select" style="left:283px;top:956px;width:151px"><span></span><svg class="arrows" viewBox="0 0 8 14"><path d="M0 6 4 1l4 5zM0 8l4 5 4-5z" fill="#222"/></svg></div>
  <div class="abs lbl" style="left:155px;top:1013px">Order Ship Rule</div>
  <div class="abs field select" style="left:283px;top:1005px;width:151px">Partials<svg class="arrows" viewBox="0 0 8 14"><path d="M0 6 4 1l4 5zM0 8l4 5 4-5z" fill="#222"/></svg></div>
  <div class="abs req" style="left:443px;top:1017px">*</div>
  <div class="abs lbl" style="left:168px;top:1060px">Line Ship Rule</div>
  <div class="abs field select" style="left:283px;top:1052px;width:151px">Partials<svg class="arrows" viewBox="0 0 8 14"><path d="M0 6 4 1l4 5zM0 8l4 5 4-5z" fill="#222"/></svg></div>
  <div class="abs req" style="left:443px;top:1064px">*</div>

  <div class="abs lbl" style="left:487px;top:823px">Request Date</div>
  <div class="abs field select" style="left:598px;top:815px;width:151px">1/07/2018<svg width="14" height="14" viewBox="0 0 14 14"><rect x="1" y="2" width="12" height="11" fill="none" stroke="#222" stroke-width="1.4"/><path d="M1 5h12M4 1v3M10 1v3M4 7.5h6M4 10h6M7 5v8" stroke="#222" stroke-width="1"/></svg></div>
  <div class="abs lbl" style="left:482px;top:870px">Freight&nbsp; Terms</div>
  <div class="abs field select" style="left:598px;top:862px;width:151px">Collect<svg class="arrows" viewBox="0 0 8 14"><path d="M0 6 4 1l4 5zM0 8l4 5 4-5z" fill="#222"/></svg></div>
  <div class="abs lbl" style="left:502px;top:917px">Freight&nbsp; Cal</div>
  <div class="abs field select" style="left:598px;top:909px;width:151px"><span></span><svg class="arrows" viewBox="0 0 8 14"><path d="M0 6 4 1l4 5zM0 8l4 5 4-5z" fill="#222"/></svg></div>

  <div class="abs lbl" style="left:779px;top:821px">Customer Ship To</div>
  <div class="abs field" style="left:916px;top:811px;width:151px"></div>
  <div class="abs" style="left:1079px;top:820px;font-size:15px">/</div>
  <div class="abs field" style="left:1091px;top:811px;width:42px"></div>
  <svg class="abs" style="left:1123px;top:920px" width="11" height="13" viewBox="0 0 11 13"><rect x="0" y="5" width="11" height="8" rx="1" fill="#7ccc3a"/><path d="M2.5 5V3.5a3 3 0 0 1 6 0V5" stroke="#7ccc3a" stroke-width="1.8" fill="none"/></svg>

  <div class="abs" style="left:0;width:1300px;top:1168px;text-align:center;font-size:15px;font-weight:700;color:#333">Click Search, or enter property values and click <span style="color:var(--link)">Apply</span></div>
</div>
</body>
</html>
```